brqnal new business card design project

we need a new business card design. you can view info about us @ brqnal-example.com. i have attached an example of our previous card with our previous name that we no longer use. We really liked the design, colors etc. look below to see more info about this project. it asks for a limited number of words. please see our website for more info about our compnay.

Target Market(s)

law enforcement

Contact Information for Business Card

i have uploaded an example of what we used before that we liked.

Font styles to use
Serif

```html
<!DOCTYPE html>
<html lang="en">
<head>
<meta charset="utf-8">
<title>Brqnal business card</title>
<link rel="stylesheet" href="https://fonts.googleapis.com/css2?family=Josefin+Sans:wght@300;400;700&display=swap">
<style>
  :root {
    --bg: #1f2124;
    --navy: #1d4f6b;
    --navy-deep: #103448;
    --navy-light: #2a6685;
    --paper: #ffffff;
    --ink: #2b2b2b;
    --grey: #8a8f94;
    --strip: #e6e8ea;
  }
  * { margin: 0; padding: 0; box-sizing: border-box; }
  html, body { width: 1200px; height: 900px; overflow: hidden; }
  body {
    background: var(--bg);
    font-family: "Josefin Sans", sans-serif;
    position: relative;
  }
  .card {
    position: absolute;
    background: var(--paper);
    border-radius: 22px;
    overflow: hidden;
  }

  /* Front: vertical contact card */
  .card-front { left: 120px; top: 170px; width: 320px; height: 560px; }
  .front-head {
    position: absolute; left: 0; top: 0; width: 100%; height: 240px;
    background: linear-gradient(160deg, var(--navy-light), var(--navy-deep));
    display: flex; align-items: center; justify-content: center;
  }
  .front-head .wordmark { color: var(--paper); font-size: 46px; }
  .front-strip {
    position: absolute; left: 0; top: 240px; width: 100%; height: 14px;
    background: var(--strip);
  }
  .front-strip::after {
    content: ""; position: absolute; right: 0; top: 0; width: 70px; height: 14px;
    background: var(--navy);
  }
  .person { position: absolute; left: 34px; top: 284px; }
  .person-name { color: var(--navy); font-weight: 700; font-size: 22px; }
  .person-title { color: var(--grey); font-size: 13px; margin-top: 4px; }
  .person-rule { width: 150px; height: 2px; background: var(--navy); margin-top: 8px; }
  .contacts { position: absolute; left: 34px; top: 372px; list-style: none; }
  .contacts li {
    display: flex; align-items: flex-start; gap: 12px;
    color: var(--grey); font-size: 16px; line-height: 1.3; margin-bottom: 12px;
  }
  .contacts .icon {
    flex: none; width: 20px; height: 20px; border-radius: 3px;
    background: var(--navy); display: flex; align-items: center; justify-content: center;
  }

  /* Back: horizontal brand card */
  .card-back { left: 520px; top: 300px; width: 560px; height: 320px; }
  .back-logo {
    position: absolute; left: 0; top: 0; width: 100%; height: 210px;
    display: flex; align-items: center; justify-content: center;
  }
  .back-logo .wordmark { color: var(--ink); font-size: 68px; }
  .back-strip {
    position: absolute; left: 230px; top: 210px; width: 200px; height: 14px;
    background: var(--strip);
  }
  .back-band {
    position: absolute; left: 0; top: 224px; width: 100%; height: 96px;
    background: linear-gradient(180deg, var(--navy-light), var(--navy));
    display: flex; align-items: center; justify-content: center;
  }
  .back-band::before, .back-band::after {
    content: ""; position: absolute; top: 0; height: 14px; background: var(--navy-deep);
  }
  .back-band::before { left: 0; width: 230px; top: -14px; }
  .back-band::after { right: 0; width: 130px; top: -14px; }
  .back-url { color: var(--paper); font-size: 22px; letter-spacing: 0.5px; }

  .wordmark { font-weight: 300; letter-spacing: 4px; }
</style>
</head>
<body>

  <section class="card card-front" aria-label="Business card front">
    <div class="front-head"><span class="wordmark">BRQNAL</span></div>
    <div class="front-strip"></div>

    <div class="person">
      <p class="person-name">Dana Whitcombe</p>
      <p class="person-title">Founder/chief Executive Officer</p>
      <div class="person-rule"></div>
    </div>

    <ul class="contacts">
      <li>
        <span class="icon"><svg width="12" height="12" viewBox="0 0 12 12"><path d="M6 1a3.5 3.5 0 0 0-3.5 3.5C2.5 7.5 6 11 6 11s3.5-3.5 3.5-6.5A3.5 3.5 0 0 0 6 1z" fill="#fff"/><circle cx="6" cy="4.5" r="1.3" fill="#1d4f6b"/></svg></span>
        <span>4128 Meridian Lane<br>Austin, TX 78701</span>
      </li>
      <li>
        <span class="icon"><svg width="12" height="12" viewBox="0 0 12 12"><path d="M3 1.5l2 2-1 1.2a6 6 0 0 0 3.3 3.3l1.2-1 2 2-1.3 1.5C5.5 10.5 1.5 6.5 1.5 2.8z" fill="#fff"/></svg></span>
        <span>555.014.2290</span>
      </li>
      <li>
        <span class="icon"><svg width="12" height="12" viewBox="0 0 12 12"><rect x="1.5" y="3" width="9" height="6" fill="#fff"/><path d="M1.5 3l4.5 3.5L10.5 3" fill="none" stroke="#1d4f6b" stroke-width="0.9"/></svg></span>
        <span>info@brqnal-example.com</span>
      </li>
      <li>
        <span class="icon"><svg width="12" height="12" viewBox="0 0 12 12" fill="none" stroke="#fff" stroke-width="1"><circle cx="6" cy="6" r="4.5"/><ellipse cx="6" cy="6" rx="2" ry="4.5"/><path d="M1.5 6h9"/></svg></span>
        <span>www.brqnal-example.com</span>
      </li>
    </ul>
  </section>

  <section class="card card-back" aria-label="Business card back">
    <div class="back-logo"><span class="wordmark">BRQNAL</span></div>
    <div class="back-strip"></div>
    <div class="back-band"><span class="back-url">www.brqnal-example.com</span></div>
  </section>

</body>
</html>
```